Redesign of Form/Document Navigation Page

I need a redesign of our document and navigation bar on the left. We want the same navigation bar layout/setup but want the buttons and typography to be simple and matching all over. The form needs to be aesthetically pleasing and fit within the page.

1st attachment is our Direct Deposit and the second is the form continued.

```html
<!DOCTYPE html>
<html lang="en">
<head>
<meta charset="utf-8">
<title>Northgate Patrol Services – Direct Deposit</title>
<link href="https://fonts.googleapis.com/css2?family=Inter:wght@400;500;600;700&display=swap" rel="stylesheet">
<style>
:root{
  --navy:#1b3f8f;
  --navy-soft:#eef2fa;
  --gold:#f5a81c;
  --page:#f3f4f8;
  --white:#ffffff;
  --line:#e1e3ea;
  --field-line:#d3d6de;
  --text:#5f6370;
  --label:#3f4450;
  --heading:#1f2a44;
}
*{box-sizing:border-box;margin:0;padding:0}
html,body{width:1200px;height:1013px;overflow:hidden}
body{position:relative;background:var(--page);font-family:"Inter",Arial,sans-serif;color:var(--text)}
.abs{position:absolute}

/* Header */
.site-header{left:0;top:0;width:1200px;height:88px;background:var(--white);box-shadow:0 1px 3px rgba(0,0,0,.07);display:flex;align-items:center;justify-content:space-between;padding:0 28px 0 25px}
.brand{display:flex;align-items:center;gap:12px}
.brand-mark{width:44px;height:44px;background:var(--navy);border-radius:6px}
.brand-name{font-weight:700;font-size:17px;line-height:20px;color:var(--gold);letter-spacing:.3px}
.top-nav{display:flex;align-items:center;gap:18px;font-size:12px;font-weight:500;color:#5f6370}
.top-nav .sep{color:#c3c6cf}
.power{width:30px;height:26px;background:var(--navy);border-radius:4px;display:flex;align-items:center;justify-content:center}

/* Back tab */
.back-tab{left:25px;top:112px;height:32px;padding:0 16px;background:var(--navy);color:#fff;font-size:11.5px;font-weight:600;letter-spacing:.4px;display:flex;align-items:center;border-radius:6px 6px 0 0}

/* Sidebar */
.sidebar{left:25px;top:144px;width:246px;background:var(--white);border:1px solid var(--line);border-radius:0 6px 6px 6px;overflow:hidden}
.nav-item{height:91px;border-bottom:1px solid var(--line);display:flex;align-items:center;padding-left:18px;gap:14px;font-size:11.5px;font-weight:600;letter-spacing:.3px;color:var(--label);border-left:3px solid transparent}
.nav-item:last-child{border-bottom:none}
.nav-item.active{background:var(--navy-soft);border-left-color:var(--navy);color:var(--navy)}
.nav-icon{width:46px;height:46px;flex:none}

/* Panel */
.panel{left:286px;top:144px;width:889px;height:736px;background:var(--white);border:1px solid var(--line);border-radius:6px;padding:26px 28px}
.section-title{font-size:17px;font-weight:600;color:var(--heading);display:flex;align-items:center;gap:10px}
.section-title::before{content:"";width:4px;height:18px;border-radius:2px;background:var(--gold)}
.section-title.manager::before{background:var(--navy)}
.terms{margin-top:14px;font-size:11.5px;line-height:20px;color:var(--text)}
.terms + .terms{margin-top:10px}

.form-row{display:flex;justify-content:space-between;margin-top:20px}
.field-group{display:flex;flex-direction:column;gap:6px}
.field-label{font-size:11.5px;font-weight:500;color:var(--label)}
.field{background:#fff;border:1px solid var(--field-line);border-radius:6px;height:36px}

.btn{height:40px;padding:0 26px;border-radius:6px;font-size:12.5px;font-weight:600;letter-spacing:.5px;color:#fff;display:inline-flex;align-items:center;justify-content:center}
.btn-primary{background:var(--navy)}
.btn-accent{background:var(--gold)}
.accept-row{margin-top:18px}

.manager-title{margin-top:26px}
.manager-box{margin-top:14px;border:1px solid var(--line);border-radius:6px;padding:16px 20px;display:grid;grid-template-columns:300px 1fr;column-gap:36px;row-gap:12px;background:#fafbfd}
.manager-box .comments .field{height:84px}
.manager-actions{grid-column:1 / -1;display:flex;justify-content:flex-end}

/* Footer */
.site-footer{left:0;top:952px;width:1200px;height:61px;background:var(--navy);display:flex;align-items:center;justify-content:space-between;padding:0 30px 0 25px}
.copyright{font-size:11px;color:#fff}
.social{display:flex;gap:8px}
.social span{width:30px;height:30px;border:1.5px solid #fff;border-radius:50%}
</style>
</head>
<body>

<header class="site-header abs">
  <div class="brand">
    <div class="brand-mark"></div>
    <div class="brand-name">NORTHGATE PATROL<br>SERVICES</div>
  </div>
  <nav class="top-nav">
    <span>HOME</span><span class="sep">|</span><span>HELP</span>
    <span class="power"><svg width="12" height="12" viewBox="0 0 12 12"><path d="M3.6 3a4 4 0 1 0 4.8 0" fill="none" stroke="#fff" stroke-width="1.6"/><line x1="6" y1="1" x2="6" y2="6" stroke="#fff" stroke-width="1.6"/></svg></span>
  </nav>
</header>

<div class="back-tab abs">BACK TO PROFILE</div>

<aside class="sidebar abs">
  <div class="nav-item active">
    <svg class="nav-icon" viewBox="0 0 46 46"><circle cx="23" cy="23" r="22" fill="#1b3f8f"/><rect x="12" y="16" width="22" height="14" rx="2" fill="none" stroke="#fff" stroke-width="1.8"/><circle cx="23" cy="23" r="3" fill="none" stroke="#fff" stroke-width="1.8"/></svg>
    DIRECT DEPOSIT</div>
  <div class="nav-item">
    <svg class="nav-icon" viewBox="0 0 46 46"><circle cx="23" cy="23" r="22" fill="none" stroke="#1b3f8f" stroke-width="1.5"/><path d="M13 23a10 10 0 0 1 17-7M33 23a10 10 0 0 1-17 7" fill="none" stroke="#1b3f8f" stroke-width="1.8"/><circle cx="23" cy="23" r="3" fill="#1b3f8f"/></svg>
    CHANGE W-4</div>
  <div class="nav-item">
    <svg class="nav-icon" viewBox="0 0 46 46"><circle cx="23" cy="23" r="22" fill="none" stroke="#1b3f8f" stroke-width="1.5"/><rect x="15" y="12" width="16" height="22" rx="2" fill="none" stroke="#1b3f8f" stroke-width="1.8"/><path d="M18 18h10M18 22h10M18 26h7" stroke="#1b3f8f" stroke-width="1.5"/></svg>
    LABOUR CODE</div>
  <div class="nav-item">
    <svg class="nav-icon" viewBox="0 0 46 46"><circle cx="23" cy="23" r="22" fill="none" stroke="#1b3f8f" stroke-width="1.5"/><circle cx="21" cy="18" r="4.5" fill="none" stroke="#1b3f8f" stroke-width="1.8"/><path d="M12 33c0-6 4-8 9-8 3 0 5 1 6 2" fill="none" stroke="#1b3f8f" stroke-width="1.8"/><path d="M31 26v8M27 30h8" stroke="#1b3f8f" stroke-width="1.8"/></svg>
    PERSONAL INFO</div>
  <div class="nav-item">
    <svg class="nav-icon" viewBox="0 0 46 46"><circle cx="23" cy="23" r="22" fill="none" stroke="#1b3f8f" stroke-width="1.5"/><circle cx="16" cy="16" r="2" fill="none" stroke="#1b3f8f" stroke-width="1.5"/><circle cx="16" cy="23" r="2" fill="none" stroke="#1b3f8f" stroke-width="1.5"/><circle cx="16" cy="30" r="2" fill="none" stroke="#1b3f8f" stroke-width="1.5"/><path d="M21 16h11M21 23h11M21 30h11" stroke="#1b3f8f" stroke-width="1.8"/></svg>
    APPRAISEL &amp; REVIEW</div>
  <div class="nav-item">
    <svg class="nav-icon" viewBox="0 0 46 46"><circle cx="23" cy="23" r="22" fill="none" stroke="#1b3f8f" stroke-width="1.5"/><rect x="15" y="13" width="16" height="20" rx="2" fill="none" stroke="#1b3f8f" stroke-width="1.8"/><path d="M18 19h10M18 23h10M18 27h6" stroke="#1b3f8f" stroke-width="1.5"/></svg>
    WRITE UP-SLIP</div>
  <div class="nav-item">
    <svg class="nav-icon" viewBox="0 0 46 46"><circle cx="23" cy="23" r="22" fill="none" stroke="#1b3f8f" stroke-width="1.5"/><path d="M14 33v-5h3v5zM19 33v-8h3v8zM24 33v-11h3v11zM29 33v-14h3v14z" fill="#1b3f8f"/><path d="M13 26l7-6 4 3 8-8" fill="none" stroke="#1b3f8f" stroke-width="1.8"/></svg>
    EMPLOYEE PERFORMANCE</div>
</aside>

<main class="panel abs">
  <h1 class="section-title">IMPORTANT! Please read and sign before completing and submitting.</h1>
  <p class="terms">I hereby authorize NORTHGATE PATROL SERVICES to deposit any amounts owed me, as instructed by my employer, by initiating credit entries to my account at the financial institution (hereinafter "Bank") indicated on this form. Further. I authorize Bank to accept and to credit any credit entries indicated by NORTHGATE PATROL SERVICES to my account. In the even that NORTHGATE PATROL SERVICES deposits funds erroneously into my account. I authorize NORTHGATE PATROL SERVICES to debit my account for an amount not to exceed the original amount of the erroneous credit.</p>
  <p class="terms">This authorization is to remain in full force and effect until NORTHGATE PATROL SERVICES and Bank have received written notice from me of its termination in such time and in such manner as to afford NORTHGATE PATROL SERVICES and Bank reasonable opportunity to act on it.</p>

  <div class="form-row">
    <div class="field-group" style="width:300px">
      <label class="field-label">Employee Name:</label>
      <div class="field"></div>
    </div>
    <div class="field-group" style="width:200px">
      <label class="field-label">Sign Date:</label>
      <div class="field"></div>
    </div>
  </div>
  <div class="form-row" style="margin-top:14px">
    <div class="field-group" style="width:300px">
      <label class="field-label">Employee Signature</label>
      <div class="field" style="height:44px"></div>
    </div>
  </div>
  <div class="accept-row"><span class="btn btn-primary">ACCEPT DOCUMENT</span></div>

  <h2 class="section-title manager manager-title">Only Payroll Manager Signs Below</h2>
  <section class="manager-box">
    <div class="field-group">
      <label class="field-label">Company Name:</label>
      <div class="field"></div>
      <label class="field-label" style="margin-top:6px">Employee File Number:</label>
      <div class="field"></div>
    </div>
    <div class="field-group comments">
      <label class="field-label">Comments:</label>
      <div class="field"></div>
    </div>
    <div class="manager-actions"><span class="btn btn-accent">SUBMIT</span></div>
  </section>
</main>

<footer class="site-footer abs">
  <p class="copyright">Copyright © 2016 NPS. All Rights Reserved.</p>
  <div class="social"><span></span><span></span><span></span><span></span><span></span></div>
</footer>

</body>
</html>
```